Verdant Systems Business Card

want the back of card to be blue- with the logo in the center
front of card- info plus logo (info being mailing address, email address, and website address )
4 different names with titles to have on cards
1) Calvin Borsted - Owner
2) Naomi Trelvik- Customer Relationship Specialist
3) Felix Andrade- Vice President of Sales
4) Owen Markby- Chief Technology Officer

Target Market(s)

tech company in the government/probation office industry

Industry/Entity Type

Government Office

Contact Information for Business Card

1) Calvin Borsted - Owner

Colors
0355a3
ffffff

Requirements
Must have
• back side should be blue, with the logo placed in the center
• front side needs to include both the logo, as well as company info (info should include website address, email address, and mailing address)

```html
<!DOCTYPE html>
<html lang="en">
<head>
<meta charset="utf-8">
<title>Verdant Systems Business Card</title>
<link href="https://fonts.googleapis.com/css2?family=Crimson+Text:wght@600&family=Roboto:wght@400;500&display=swap" rel="stylesheet">
<style>
  :root {
    --brand-blue: #0355a3;
    --grey: #808084;
    --text-grey: #4a4a4e;
    --rule-grey: #c9c9cc;
    --white: #ffffff;
    --backdrop: #ecebe8;
  }
  * { margin: 0; padding: 0; box-sizing: border-box; }
  html, body {
    width: 1125px; height: 1200px; overflow: hidden;
    background: var(--backdrop);
    font-family: "Roboto", Arial, sans-serif;
  }
  .canvas { position: relative; width: 1125px; height: 1200px; }
  .card {
    position: absolute; left: 171px; width: 826px; height: 472px;
    box-shadow: 0 3px 8px rgba(0,0,0,0.25);
  }
  .card-front { top: 106px; background: var(--white); }
  .card-back { top: 639px; background: var(--brand-blue); }

  .brand-name {
    position: absolute; font-family: "Roboto", Arial, sans-serif;
    font-weight: 500; font-size: 38px; letter-spacing: 1px;
    white-space: nowrap; transform: translate(-50%, -50%);
  }
  .card-front .brand-name { left: 221px; top: 229px; color: var(--brand-blue); }
  .card-back .brand-name { left: 413px; top: 233px; color: var(--white); font-size: 46px; }

  .divider {
    position: absolute; left: 410px; top: 128px; width: 1px; height: 200px;
    background: var(--rule-grey);
  }
  .person-name {
    position: absolute; left: 450px; top: 136px;
    font-family: "Crimson Text", Georgia, serif; font-weight: 600;
    font-size: 34px; color: var(--brand-blue); line-height: 1;
  }
  .person-title {
    position: absolute; left: 451px; top: 172px;
    font-size: 20px; font-weight: 500; color: var(--grey);
  }
  .contact-list { position: absolute; left: 450px; top: 212px; list-style: none; }
  .contact-item {
    display: flex; align-items: center; height: 27px;
    font-size: 19.5px; color: var(--text-grey); white-space: nowrap;
  }
  .contact-item svg { width: 18px; height: 18px; margin-right: 11px; fill: var(--brand-blue); flex: none; }

  .web-band {
    position: absolute; left: 0; top: 393px; width: 100%; height: 41px;
    display: flex;
  }
  .web-band-main {
    width: 696px; background: var(--brand-blue); color: var(--white);
    display: flex; align-items: center; justify-content: center;
    font-size: 19px; letter-spacing: 3px; padding-left: 80px;
  }
  .web-band-accent { flex: 1; background: var(--grey); }
  .band-mark {
    position: absolute; left: 682px; top: 2px; width: 37px; height: 37px;
    border-radius: 50%; background: var(--white); border: 3px solid var(--brand-blue);
  }
  .back-web {
    position: absolute; left: 0; width: 100%; top: 403px; text-align: center;
    color: var(--white); font-size: 19px; letter-spacing: 3px;
  }
</style>
</head>
<body>
<div class="canvas">
  <section class="card card-front">
    <div class="brand-name">Verdant Systems</div>
    <div class="divider"></div>
    <div class="person-name">Calvin Borsted</div>
    <div class="person-title">Owner</div>
    <ul class="contact-list">
      <li class="contact-item">
        <svg viewBox="0 0 24 24" aria-hidden="true"><path d="M6.6 10.8a15.1 15.1 0 0 0 6.6 6.6l2.2-2.2a1 1 0 0 1 1-.25 11.4 11.4 0 0 0 3.6.57 1 1 0 0 1 1 1V20a1 1 0 0 1-1 1A17 17 0 0 1 3 4a1 1 0 0 1 1-1h3.5a1 1 0 0 1 1 1c0 1.25.2 2.450.57 3.57a1 1 0 0 1-.25 1z"/></svg>
        415-208-3317
      </li>
      <li class="contact-item">
        <svg viewBox="0 0 24 24" aria-hidden="true"><path d="M7 1h10a2 2 0 0 1 2 2v18a2 2 0 0 1-2 2H7a2 2 0 0 1-2-2V3a2 2 0 0 1 2-2zm0 3v14h10V4zm5 15.5a1.2 1.2 0 1 0 0 2.4 1.2 1.2 0 0 0 0-2.4z"/></svg>
        415-730-9142
      </li>
      <li class="contact-item">
        <svg viewBox="0 0 24 24" aria-hidden="true"><path d="M2 6h20v12H2zm1.5 1.2v.4L12 13l8.5-5.4v-.4z"/></svg>
        info@verdantsystems.com
      </li>
      <li class="contact-item">
        <svg viewBox="0 0 24 24" aria-hidden="true"><path d="M12 2a7 7 0 0 0-7 7c0 5.2 7 13 7 13s7-7.8 7-13a7 7 0 0 0-7-7zm0 9.5A2.5 2.5 0 1 1 12 6.5a2.5 2.5 0 0 1 0 5z"/></svg>
        1840 Harlow Ave, Denver, CO 80204
      </li>
    </ul>
    <div class="web-band">
      <div class="web-band-main">www.verdantsystems.com</div>
      <div class="web-band-accent"></div>
      <div class="band-mark"></div>
    </div>
  </section>

  <section class="card card-back">
    <div class="brand-name">Verdant Systems</div>
    <div class="back-web">www.verdantsystems.com</div>
  </section>
</div>
</body>
</html>
```